Business Card Design

Company is a Commercial Building Company specialising in New Construction and existing refurbishments

Industry/Entity Type

Business

Contact Information for Business Card

Liam Porter
Construction Manager
E Liam@marshbuilding.com.au
M 0400 213 594
Mail 14 Tarrant Rise Halden Bay WA 6209

```html
<!DOCTYPE html>
<html lang="en">
<head>
<meta charset="utf-8">
<title>Marsh Building &amp; Construction – Business Card</title>
<link rel="stylesheet" href="https://fonts.googleapis.com/css2?family=Montserrat:wght@700&family=Roboto:wght@300;400&display=swap">
<style>
  :root {
    --cyan: #06b8d7;
    --orange: #f7941d;
    --navy: #1e2a3a;
    --grey: #4a4f55;
    --white: #ffffff;
    --backdrop: #e9e7e3;
    --photo-light: #c9d3cf;
    --photo-mid: #8fa07f;
    --photo-dark: #4d6a3a;
  }
  * { margin: 0; padding: 0; box-sizing: border-box; }
  html, body {
    width: 1200px; height: 1023px; overflow: hidden;
    background: var(--backdrop);
    font-family: "Roboto", Arial, sans-serif;
  }
  .stage { position: relative; width: 1200px; height: 1023px; }
  .card {
    position: absolute; top: 357px;
    width: 540px; height: 309px;
    overflow: hidden;
    box-shadow: 0 6px 18px rgba(0,0,0,0.18);
  }
  .card--front { left: 40px; background: var(--white); }
  .card--back { left: 620px; background: var(--cyan); }

  .front__photo { position: absolute; left: 0; top: 0; width: 540px; height: 175px; }

  .brand { position: absolute; display: flex; align-items: center; gap: 10px; }
  .brand__mark { width: 34px; height: 34px; background: var(--orange); flex: none; }
  .brand__name {
    font-family: "Montserrat", Arial, sans-serif; font-weight: 700;
    font-size: 14px; line-height: 1.15; letter-spacing: 0.5px;
    text-transform: uppercase; color: var(--navy);
    white-space: nowrap;
  }
  .card--front .brand { left: 28px; top: 205px; }

  .person { position: absolute; left: 245px; top: 178px; }
  .person__name { font-size: 34px; font-weight: 300; color: var(--cyan); line-height: 1; white-space: nowrap; }
  .person__role { font-size: 12px; color: var(--grey); margin-top: 4px; }

  .contacts { position: absolute; left: 245px; top: 234px; list-style: none; }
  .contacts li {
    display: flex; align-items: center; gap: 8px;
    font-size: 12.5px; color: var(--grey); line-height: 20px; white-space: nowrap;
  }
  .contacts svg { width: 11px; height: 11px; fill: var(--cyan); flex: none; }

  .card--back .brand { left: 50%; top: 50%; transform: translate(-50%, -50%); gap: 14px; }
  .card--back .brand__mark { width: 52px; height: 52px; }
  .card--back .brand__name { font-size: 22px; }
</style>
</head>
<body>
<main class="stage">
  <section class="card card--front" aria-label="Business card front">
    <svg class="front__photo" viewBox="0 0 540 175">
      <defs>
        <linearGradient id="photoTone" x1="0" y1="0" x2="1" y2="1">
          <stop offset="0" stop-color="var(--photo-light)"/>
          <stop offset="0.55" stop-color="var(--photo-mid)"/>
          <stop offset="1" stop-color="var(--photo-dark)"/>
        </linearGradient>
        <clipPath id="photoClip">
          <path d="M0 0 H540 V95 C430 170 200 175 0 135 Z"/>
        </clipPath>
      </defs>
      <rect width="540" height="175" fill="url(#photoTone)" clip-path="url(#photoClip)" role="img" aria-label="Photo of a white multi-storey apartment building with curved balconies among trees"/>
      <path d="M0 135 C200 175 430 170 540 95" fill="none" stroke="var(--cyan)" stroke-width="5"/>
    </svg>

    <div class="brand">
      <span class="brand__mark"></span>
      <span class="brand__name">Marsh Building<br>&amp; Construction</span>
    </div>

    <div class="person">
      <p class="person__name">Liam Porter</p>
      <p class="person__role">Construction Manager</p>
    </div>

    <ul class="contacts">
      <li>
        <svg viewBox="0 0 12 12"><path d="M2.5 0.5l2 2.2-1 1.4c.7 1.5 1.9 2.7 3.4 3.4l1.4-1 2.2 2-1.2 2.5C4.8 10.6 1.4 7.2.5 2z"/></svg>
        0400 213 594
      </li>
      <li>
        <svg viewBox="0 0 12 12"><path d="M0 2h12v8H0z M0 2l6 4.5L12 2" fill="var(--cyan)" stroke="var(--white)" stroke-width="0.8"/></svg>
        Liam@marshbuilding.com.au
      </li>
      <li>
        <svg viewBox="0 0 12 12"><path d="M6 0a4 4 0 0 1 4 4c0 3-4 8-4 8S2 7 2 4a4 4 0 0 1 4-4zm0 2.5a1.5 1.5 0 1 0 0 3 1.5 1.5 0 0 0 0-3z"/></svg>
        14 Tarrant Rise Halden Bay WA 6209
      </li>
    </ul>
  </section>

  <section class="card card--back" aria-label="Business card back">
    <div class="brand">
      <span class="brand__mark"></span>
      <span class="brand__name">Marsh Building<br>&amp; Construction</span>
    </div>
  </section>
</main>
</body>
</html>
```